Card Design for my dog training business Brightpaw Obedience

Need a business card design for my dog training business with my new logo. Want the card to come off professional yet fun. Want it to be very eye catchy as well. I normally have these at vet clinics, pet stores, and groomers. so need it to look better than my competitors.
Target Market(s)
dog owners
Industry/Entity Type
Dog Training
Contact Information for Business Card
needs logo, my name and info
Font styles to use
Serif
Colors
0255a3
ffffff
ec1f27
000000
333333
fbfbfb
Requirements
Must have
- Brightpaw Obedience
- Felix Orland
- 415 903 2276
- info@brightpawobedience.example
- www.brightpawobedience.example

```html
<!DOCTYPE html>
<html lang="en">
<head>
<meta charset="utf-8">
<title>Brightpaw Obedience – Business Card</title>
<link href="https://fonts.googleapis.com/css2?family=Noto+Serif:wght@400;700&family=EB+Garamond:ital@1&display=swap" rel="stylesheet">
<style>
  :root {
    --ink: #000000;
    --ink-soft: #333333;
    --paper: #fbfbfb;
    --white: #ffffff;
    --silver: #d2d2d2;
    --stage: #e6e6e6;
  }
  * { box-sizing: border-box; margin: 0; padding: 0; }
  html, body {
    width: 1200px; height: 900px; overflow: hidden;
    background: var(--stage);
    font-family: "Noto Serif", Georgia, serif;
  }
  .card {
    position: absolute; left: 270px; width: 660px; height: 377px;
    overflow: hidden;
    box-shadow: 0 10px 28px rgba(0,0,0,.22);
  }

  /* Front side */
  .card-front { top: 48px; background: var(--ink); color: var(--white); }
  .front-artwork {
    position: absolute; left: 40px; top: 70px; width: 400px; height: 307px;
    background: radial-gradient(ellipse at 60% 45%, #a8a8a8 0%, #5a5a5a 40%, #1a1a1a 75%, #000 100%);
    border-radius: 45% 50% 0 0;
  }
  .front-brand {
    position: absolute; right: 40px; top: 64px; width: 230px;
    font-size: 30px; line-height: 1.2; text-align: right; color: var(--silver);
  }
  .front-web {
    position: absolute; right: 40px; bottom: 36px;
    font-size: 15px; letter-spacing: .4px; color: var(--silver);
  }

  /* Back side */
  .card-back { top: 475px; background: var(--paper); color: var(--ink); }
  .back-brand {
    position: absolute; left: 40px; top: 122px; width: 190px;
    font-size: 22px; line-height: 1.25; text-align: center; color: var(--ink);
  }
  .back-divider {
    position: absolute; left: 248px; top: 80px; width: 1.5px; height: 150px;
    background: var(--ink);
  }
  .contact { position: absolute; left: 274px; top: 84px; }
  .contact-name { font-size: 24px; font-weight: 700; letter-spacing: .3px; line-height: 30px; }
  .contact-company { font-size: 16px; color: var(--ink-soft); margin-bottom: 10px; }
  .contact-line { display: flex; align-items: center; gap: 10px; font-size: 16px; line-height: 26px; white-space: nowrap; }
  .contact-line svg { width: 16px; height: 16px; flex: none; }
  .tagline {
    position: absolute; left: 0; right: 0; bottom: 40px; text-align: center;
    font-family: "EB Garamond", Georgia, serif; font-style: italic;
    font-size: 21px; color: var(--ink-soft);
  }
</style>
</head>
<body>

<section class="card card-front">
  <div class="front-artwork" role="img" aria-label="Silver foil illustration of two dog heads"></div>
  <div class="front-brand">Brightpaw Obedience</div>
  <div class="front-web">www.brightpawobedience.example</div>
</section>

<section class="card card-back">
  <div class="back-brand">Brightpaw Obedience</div>
  <div class="back-divider"></div>
  <div class="contact">
    <div class="contact-name">Felix Orland</div>
    <div class="contact-company">Brightpaw Obedience</div>
    <div class="contact-line">
      <svg viewBox="0 0 24 24"><path d="M6.6 10.8a15 15 0 0 0 6.6 6.6l2.2-2.2a1 1 0 0 1 1-.25 11.4 11.4 0 0 0 3.6.6 1 1 0 0 1 1 1V20a1 1 0 0 1-1 1A17 17 0 0 1 3 4a1 1 0 0 1 1-1h3.5a1 1 0 0 1 1 1c0 1.25.2 2.450.6 3.6a1 1 0 0 1-.25 1z" fill="#000"/></svg>
      <span>415 903 2276</span>
    </div>
    <div class="contact-line">
      <svg viewBox="0 0 24 24"><rect x="2" y="5" width="20" height="14" fill="#000"/><path d="M2 5l10 8 10-8" stroke="#fff" stroke-width="1.6" fill="none"/></svg>
      <span>info@brightpawobedience.example</span>
    </div>
    <div class="contact-line">
      <svg viewBox="0 0 24 24"><circle cx="12" cy="12" r="10" fill="#000"/><circle cx="12" cy="12" r="4" fill="#fff"/></svg>
      <span>www.brightpawobedience.example</span>
    </div>
  </div>
  <p class="tagline">“Building better manners one lesson at a time.”</p>
</section>

</body>
</html>
```